Velvet Circle club

We are looking to redesign the user interface of our mobile app “Velvet Circle”, which is the official rewards program for our luxury casino brand, Kestrane Harbour.
Our goal is to give the app a more elegant, premium, and user-friendly design that reflects the exclusivity of our brand and the luxury experience we offer our VIP clientele.
What We Need:
A complete UI design for the app’s main screens, including:
Splash Screen
01 Login / Signup Screen
02 Home Dashboard
Buttons -
Home / my card / my wallet / my booking / my host
My wallet / my offer / lucky game / my taxi / entertainment / online
03 Profile screen
04 My wallet
05 My offer
06Packages
07 My booking
08 My host
09 My card
we attached our privies app all the screen for you reference
Inspiration:
Think of luxury brands like Dunmore-Vale, Corvix Onyx, or high-end lifestyle apps. Clean interfaces, classy animations, and a sense of exclusivity are key.
We’re excited to see fresh, innovative takes that elevate the app to a truly world-class luxury experience for our users.
Thank you!
Casino

```html
<!DOCTYPE html>
<html lang="en">
<head>
<meta charset="utf-8">
<title>Velvet Circle club – App Screens</title>
<link href="https://fonts.googleapis.com/css2?family=Montserrat:wght@600;700;800;900&family=Quicksand:wght@400;500;600&display=swap" rel="stylesheet">
<style>
:root{
  --gold:#f7a823;
  --red:#e41f26;
  --screen:#232323;
  --black:#0a0a0a;
  --card:#2c2c2c;
  --white:#ffffff;
  --muted:#d8d8d8;
}
*{box-sizing:border-box;margin:0;padding:0}
html,body{width:1200px;height:563px;overflow:hidden;background:#fff}
body{position:relative;font-family:"Quicksand",sans-serif;color:var(--white)}
.screen{position:absolute;top:60px;width:251px;height:446px;background:var(--screen);overflow:hidden}
.s-login-a{left:37px}
.s-login-b{left:331px}
.s-home{left:612px}
.s-gaming{left:896px}

/* login */
.brand{position:absolute;top:18px;left:0;right:0;text-align:center}
.brand-mark{width:24px;height:24px;border-radius:50%;background:var(--red);margin:0 auto 8px}
.brand-name{font-family:"Montserrat",sans-serif;font-weight:800;font-size:21px;color:var(--gold);letter-spacing:.5px;line-height:1}
.brand-sub{font-family:"Montserrat",sans-serif;font-weight:800;font-size:10px;color:var(--gold);letter-spacing:2px;margin-top:5px}
.block{position:absolute;left:0;right:0;text-align:center}
.h-main{font-family:"Montserrat",sans-serif;font-weight:900;color:var(--gold);font-size:16px;letter-spacing:.3px}
.h-sub{font-family:"Montserrat",sans-serif;font-weight:900;color:var(--gold);font-size:12px}
.lead{font-weight:400;font-size:10px;line-height:14px;color:var(--white);margin-top:8px}
.btn{display:block;margin:0 auto;width:89px;height:29px;border-radius:15px;background:var(--red);font-family:"Montserrat",sans-serif;font-weight:900;font-size:12px;line-height:29px;color:#fff}
.base{position:absolute;left:0;top:336px;width:251px;height:110px}
.or{position:absolute;top:363px;left:0;right:0;text-align:center;font-family:"Montserrat",sans-serif;font-weight:600;font-size:11px}
.temp-note{position:absolute;top:389px;left:0;right:0;text-align:center;font-size:8.5px}
.btn-outline{position:absolute;top:410px;left:37px;width:176px;height:21px;border:1px solid var(--red);border-radius:11px;text-align:center;font-family:"Montserrat",sans-serif;font-weight:700;font-size:8px;line-height:19px;color:var(--red)}

/* app chrome */
.topbar{position:absolute;top:0;left:0;width:251px;height:31px;background:var(--black);display:flex;align-items:center;padding:0 9px}
.topbar .dot{width:14px;height:14px;border-radius:50%;background:var(--red);margin-left:9px}
.topbar .title{font-family:"Montserrat",sans-serif;font-weight:800;font-size:12px;margin-left:10px}
.topbar .bell{margin-left:auto}
.tabbar{position:absolute;bottom:0;left:0;width:251px;height:49px;background:var(--black);display:flex;justify-content:space-around;padding-top:9px}
.tab{display:flex;flex-direction:column;align-items:center;width:50px;font-size:7.5px;font-weight:500}
.tab svg{margin-bottom:4px}

/* home */
.hero{position:absolute;top:31px;left:0;width:251px;height:168px;background:linear-gradient(160deg,#7a4a2a 0%,#3b2218 45%,#8a3a2c 75%,#2a1410 100%)}
.hero-title{position:absolute;top:133px;left:0;right:0;text-align:center;font-family:"Montserrat",sans-serif;font-weight:900;font-size:11.5px}
.grid{position:absolute;top:225px;left:0;width:251px;display:grid;grid-template-columns:82px 86px 83px;row-gap:20px}
.tile{display:flex;flex-direction:column;align-items:center;font-size:8.5px;font-weight:500}
.tile .icon{width:43px;height:43px;border-radius:50%;background:var(--gold);display:flex;align-items:center;justify-content:center;margin-bottom:10px}

/* gaming */
.game{position:absolute;left:10px;width:231px;height:84px;background:var(--card);display:flex}
.game-img{width:71px;height:84px;flex:none}
.game-body{padding:10px 0 0 11px}
.game-title{font-family:"Montserrat",sans-serif;font-weight:700;font-size:9.5px}
.game-text{font-size:5.6px;line-height:7.2px;margin-top:4px;width:142px;color:var(--muted)}
.view{display:inline-block;margin-top:5px;background:var(--gold);color:#111;font-family:"Montserrat",sans-serif;font-weight:700;font-size:6px;padding:2px 6px}
</style>
</head>
<body>

<!-- LOGIN (device layout) -->
<section class="screen s-login-a">
  <div class="brand"><div class="brand-mark"></div><div class="brand-name">VELVET CIRCLE</div><div class="brand-sub">CLUB</div></div>
  <div class="block" style="top:143px"><div class="h-main">MEMBER LOGIN</div><p class="lead">Now you can enjoy all the excitement of the<br>casino right at your fingertips.</p></div>
  <div class="block" style="top:205px"><span class="btn">SIGN IN</span></div>
  <svg class="base" viewBox="0 0 251 110" preserveAspectRatio="none"><path d="M0 20 Q125 -12 251 20 L251 110 L0 110Z" fill="var(--black)"/></svg>
  <div class="block" style="top:265px"><div class="h-sub">NEW MEMBER LOGIN</div><p class="lead">If you are a first-time user, please go<br>through the sign-up process</p></div>
  <div class="block" style="top:321px"><span class="btn">SIGN UP</span></div>
  <div class="or">OR</div>
  <div class="temp-note">If you are with a temporary ID, sign in here</div>
  <div class="btn-outline">TEMPORARY SIGN IN</div>
</section>

<!-- LOGIN -->
<section class="screen s-login-b">
  <div class="brand"><div class="brand-mark"></div><div class="brand-name">VELVET CIRCLE</div><div class="brand-sub">CLUB</div></div>
  <div class="block" style="top:143px"><div class="h-main">MEMBER LOGIN</div><p class="lead">Now you can enjoy all the excitement of the<br>casino right at your fingertips.</p></div>
  <div class="block" style="top:205px"><span class="btn">SIGN IN</span></div>
  <svg class="base" viewBox="0 0 251 110" preserveAspectRatio="none"><path d="M0 20 Q125 -12 251 20 L251 110 L0 110Z" fill="var(--black)"/></svg>
  <div class="block" style="top:265px"><div class="h-sub">NEW MEMBER LOGIN</div><p class="lead">If you are a first-time user, please go<br>through the sign-up process</p></div>
  <div class="block" style="top:321px"><span class="btn">SIGN UP</span></div>
  <div class="or">OR</div>
  <div class="temp-note">If you are with a temporary ID, sign in here</div>
  <div class="btn-outline">TEMPORARY SIGN IN</div>
</section>

<!-- HOME -->
<section class="screen s-home">
  <header class="topbar">
    <svg width="14" height="11" viewBox="0 0 14 11"><path d="M0 1h14M0 5.5h14M0 10h14" stroke="#fff" stroke-width="1.4"/></svg>
    <span class="dot"></span>
    <svg class="bell" width="14" height="15" viewBox="0 0 14 15" fill="none" stroke="#fff" stroke-width="1.2"><path d="M3 11V7a4 4 0 0 1 8 0v4l1.5 1.5h-11Z"/><path d="M5.5 13.5a1.5 1.5 0 0 0 3 0"/></svg>
  </header>
  <div class="hero" role="img" aria-label="Photo of an elegantly dressed couple at a casino evening"></div>
  <div class="hero-title">LOREM IPSUM IS SIMPLY DUMMY</div>
  <div class="grid">
    <div class="tile"><span class="icon"><svg width="22" height="20" viewBox="0 0 22 20" fill="none" stroke="#111" stroke-width="1.6"><rect x="1" y="5" width="19" height="14" rx="2"/><path d="M3 5l11-4 2 4"/><rect x="14" y="10" width="6" height="4"/></svg></span>My Wallet</div>
    <div class="tile"><span class="icon"><svg width="22" height="22" viewBox="0 0 22 22" fill="none" stroke="#111" stroke-width="1.5"><rect x="5" y="5" width="12" height="9"/><path d="M5 8h12M11 5v9M1 20l5-3h8l5-3"/></svg></span>My Offer</div>
    <div class="tile"><span class="icon"><svg width="22" height="22" viewBox="0 0 22 22" fill="none" stroke="#111" stroke-width="1.6"><path d="M11 1l9 5v10l-9 5-9-5V6Z M2 6l9 5 9-5 M11 11v10"/></svg></span>Lucky Game</div>
    <div class="tile"><span class="icon"><svg width="22" height="20" viewBox="0 0 22 20" fill="none" stroke="#111" stroke-width="1.6"><rect x="8" y="0.5" width="6" height="3"/><path d="M4 9l2-5h10l2 5"/><rect x="2" y="9" width="18" height="6" rx="1"/><path d="M4 15v3M18 15v3"/></svg></span>My Taxi</div>
    <div class="tile"><span class="icon"><svg width="22" height="22" viewBox="0 0 22 22" fill="none" stroke="#111" stroke-width="1.5"><path d="M2 20L8 6l8 8Z"/><circle cx="15" cy="4" r="1.5"/><circle cx="19" cy="8" r="1"/><path d="M12 3v2M18 12h2"/></svg></span>Entertainment</div>
    <div class="tile"><span class="icon"><svg width="22" height="20" viewBox="0 0 22 20" fill="none" stroke="#111" stroke-width="1.6"><rect x="1" y="1" width="20" height="13" rx="1"/><path d="M11 14v4M6 19h10M5 5h6M5 8h8M5 11h4"/></svg></span>Online</div>
  </div>
  <nav class="tabbar">
    <div class="tab"><svg width="14" height="14" viewBox="0 0 14 14" fill="none" stroke="var(--gold)" stroke-width="1.2"><path d="M1 7l6-6 6 6v6H1Z"/></svg>Home</div>
    <div class="tab"><svg width="14" height="14" viewBox="0 0 14 14" fill="none" stroke="var(--gold)" stroke-width="1.2"><rect x="1" y="3" width="12" height="9" rx="1"/><path d="M1 6h12"/></svg>My Card</div>
    <div class="tab"><svg width="14" height="14" viewBox="0 0 14 14" fill="none" stroke="var(--gold)" stroke-width="1.2"><rect x="1" y="4" width="12" height="9" rx="1"/><path d="M2 4l7-3 1 3"/></svg>My Wallet</div>
    <div class="tab"><svg width="14" height="14" viewBox="0 0 14 14" fill="none" stroke="var(--gold)" stroke-width="1.2"><rect x="1" y="2" width="12" height="11"/><path d="M1 5h12M4 8h2M8 8h2M4 11h2M8 11h2"/></svg>My Booking</div>
    <div class="tab"><svg width="14" height="14" viewBox="0 0 14 14" fill="none" stroke="var(--gold)" stroke-width="1.2"><rect x="1" y="3" width="12" height="9"/><circle cx="4.5" cy="7" r="1.5"/><path d="M8 6h4M8 9h4"/></svg>Contact</div>
  </nav>
</section>

<!-- GAMING -->
<section class="screen s-gaming">
  <header class="topbar">
    <svg width="14" height="11" viewBox="0 0 14 11"><path d="M0 1h14M0 5.5h14M0 10h14" stroke="#fff" stroke-width="1.4"/></svg>
    <span class="dot"></span>
    <span class="title">GAMING</span>
    <svg class="bell" width="14" height="15" viewBox="0 0 14 15" fill="none" stroke="#fff" stroke-width="1.2"><path d="M3 11V7a4 4 0 0 1 8 0v4l1.5 1.5h-11Z"/><path d="M5.5 13.5a1.5 1.5 0 0 0 3 0"/></svg>
  </header>
  <article class="game" style="top:41px"><div class="game-img" role="img" aria-label="Photo of a dealer at a baccarat table" style="background:linear-gradient(160deg,#5a4030,#1d1512 60%,#6a1a1a)"></div><div class="game-body"><div class="game-title">BACCARAT</div><p class="game-text">Kestrane Harbour Baccarat is a very lucky game and easy to play. It is the most popular card game in Asia and Kestrane Harbour offers Baccarat Tables for All Players both High Stakes and Low stakes 24 hours.</p><span class="view">VIEW MORE</span></div></article>
  <article class="game" style="top:130px"><div class="game-img" role="img" aria-label="Photo of a roulette wheel" style="background:radial-gradient(circle at 90% 60%,#b01818,#5a0c0c 45%,#1a1a1a)"></div><div class="game-body"><div class="game-title">ROULETTE</div><p class="game-text">Kestrane Harbour Baccarat is a very lucky game and easy to play. It is the most popular card game in Asia and Kestrane Harbour offers Baccarat Tables for All Players both High Stakes and Low stakes 24 hours.</p><span class="view">VIEW MORE</span></div></article>
  <article class="game" style="top:221px"><div class="game-img" role="img" aria-label="Photo of cards dealt on a blackjack table" style="background:linear-gradient(160deg,#2e4a3e,#123228 55%,#0b2018)"></div><div class="game-body"><div class="game-title">BLACKJACK</div><p class="game-text">Kestrane Harbour Baccarat is a very lucky game and easy to play. It is the most popular card game in Asia and Kestrane Harbour offers Baccarat Tables for All Players both High Stakes and Low stakes 24 hours.</p><span class="view">VIEW MORE</span></div></article>
  <article class="game" style="top:309px"><div class="game-img" role="img" aria-label="Photo of a joker playing card" style="background:linear-gradient(160deg,#1f5a5c,#123a40 50%,#d8d8d8 90%)"></div><div class="game-body"><div class="game-title">SABONG CARDS</div><p class="game-text">Kestrane Harbour Baccarat is a very lucky game and easy to play. It is the most popular card game in Asia and Kestrane Harbour offers Baccarat Tables for All Players both High Stakes and Low stakes 24 hours.</p><span class="view">VIEW MORE</span></div></article>
  <nav class="tabbar">
    <div class="tab"><svg width="14" height="14" viewBox="0 0 14 14" fill="none" stroke="var(--gold)" stroke-width="1.2"><path d="M1 7l6-6 6 6v6H1Z"/></svg>Home</div>
    <div class="tab"><svg width="14" height="14" viewBox="0 0 14 14" fill="none" stroke="var(--gold)" stroke-width="1.2"><rect x="1" y="3" width="12" height="9" rx="1"/><path d="M1 6h12"/></svg>My Card</div>
    <div class="tab"><svg width="14" height="14" viewBox="0 0 14 14" fill="none" stroke="var(--gold)" stroke-width="1.2"><rect x="1" y="4" width="12" height="9" rx="1"/><path d="M2 4l7-3 1 3"/></svg>My Wallet</div>
    <div class="tab"><svg width="14" height="14" viewBox="0 0 14 14" fill="none" stroke="var(--gold)" stroke-width="1.2"><rect x="1" y="2" width="12" height="11"/><path d="M1 5h12M4 8h2M8 8h2M4 11h2M8 11h2"/></svg>My Booking</div>
    <div class="tab"><svg width="14" height="14" viewBox="0 0 14 14" fill="none" stroke="var(--gold)" stroke-width="1.2"><rect x="1" y="3" width="12" height="9"/><circle cx="4.5" cy="7" r="1.5"/><path d="M8 6h4M8 9h4"/></svg>Contact</div>
  </nav>
</section>

</body>
</html>
```